Veltrano.co - Polar Expeditions Specialists

We need a modern, visually striking business card for Veltrano.co, a company specialized in selling expedition cruises to the most remote regions on Earth, with a focus on the Arctic and Antarctica. The design should instantly communicate that the cardholder is an expert in polar travel. Use clean, premium aesthetics with cool tones like icy blue and white, possibly incorporating polar imagery (ice, glaciers, penguins, etc.)

Attached the logo

Contact Information for Business Card

Feels high-end and trustworthy.. Visually memorable — encourages people to keep it

Colors
0054AA
0677BA
7BADD7
CADEEF
E8F1F8

Requirements
Must have
• ice, glaciers, penguins, montains
Nice to have
• modern, transparente,

```html
<!DOCTYPE html>
<html lang="en">
<head>
<meta charset="UTF-8">
<title>Veltrano.co – Business Card</title>
<link href="https://fonts.googleapis.com/css2?family=Montserrat:wght@400;700&family=Poppins:wght@600;700&display=swap" rel="stylesheet">
<style>
  :root {
    --bg: #d3d8d8;
    --card: #ecedeb;
    --brand-blue: #3a78bd;
    --edge-blue: #2f73c0;
    --ink: #3a3b3c;
  }
  * { margin: 0; padding: 0; box-sizing: border-box; }
  html, body { width: 1200px; height: 881px; overflow: hidden; }
  body {
    background: var(--bg);
    display: flex;
    align-items: center;
    justify-content: center;
    gap: 40px;
  }
  .card {
    width: 540px;
    height: 309px;
    background: var(--card);
    border-bottom: 5px solid var(--edge-blue);
    box-shadow: 0 14px 30px rgba(0,0,0,0.12);
    position: relative;
    display: flex;
    align-items: center;
    justify-content: center;
  }
  /* Contact side */
  .contact-side { gap: 26px; }
  .identity { text-align: right; }
  .identity .name {
    font-family: "Montserrat", sans-serif;
    font-weight: 700;
    font-size: 24px;
    color: var(--brand-blue);
    letter-spacing: 0.3px;
  }
  .identity .role {
    font-family: "Montserrat", sans-serif;
    font-weight: 400;
    font-size: 15px;
    color: var(--ink);
    margin-top: 2px;
  }
  .divider { width: 2px; height: 78px; background: var(--brand-blue); }
  .contact-list { list-style: none; }
  .contact-list li {
    font-family: "Montserrat", sans-serif;
    font-size: 15px;
    color: var(--ink);
    display: flex;
    align-items: center;
    gap: 8px;
    line-height: 24px;
  }
  .contact-list svg { width: 12px; height: 12px; fill: var(--brand-blue); }
  /* Brand side */
  .brand-side { flex-direction: column; align-items: flex-start; padding-left: 70px; }
  .brand-row { display: flex; align-items: center; gap: 16px; }
  .brand-dot { width: 58px; height: 58px; border-radius: 50%; background: var(--brand-blue); }
  .brand-name {
    font-family: "Poppins", sans-serif;
    font-weight: 700;
    font-size: 54px;
    color: var(--brand-blue);
    line-height: 1;
  }
  .tagline {
    font-family: "Poppins", sans-serif;
    font-weight: 600;
    font-size: 17px;
    color: var(--brand-blue);
    margin: 8px 0 0 74px;
    letter-spacing: 0.3px;
  }
</style>
</head>
<body>
  <section class="card contact-side">
    <div class="identity">
      <div class="name">MARCUS HALE</div>
      <div class="role">Managing Director</div>
    </div>
    <div class="divider"></div>
    <ul class="contact-list">
      <li><svg viewBox="0 0 24 24" aria-hidden="true"><path d="M6.6 10.8a15 15 0 0 0 6.6 6.6l2.2-2.2a1 1 0 0 1 1-.25 11.4 11.4 0 0 0 3.6.57 1 1 0 0 1 1 1V20a1 1 0 0 1-1 1A17 17 0 0 1 3 4a1 1 0 0 1 1-1h3.5a1 1 0 0 1 1 1c0 1.25.2 2.45.57 3.57a1 1 0 0 1-.25 1z"/></svg>555 018 274</li>
      <li><svg viewBox="0 0 24 24" aria-hidden="true"><path d="M2 5h20v2l-10 6L2 7zm0 4.3 10 6 10-6V19H2z"/></svg>info@veltrano.co</li>
      <li><svg viewBox="0 0 24 24" aria-hidden="true"><circle cx="12" cy="12" r="10"/></svg>www.veltrano.co</li>
    </ul>
  </section>

  <section class="card brand-side">
    <div class="brand-row">
      <div class="brand-dot"></div>
      <div class="brand-name">Veltrano.co</div>
    </div>
    <div class="tagline">Polar Expeditions Specialists</div>
  </section>
</body>
</html>
```